Building company buisness cards

We are looking for a sharp modern new look for our business cards.
We are a New Zealand based company that specialises in house and land packages.
We have attached a photo of the current logo and would like to see if it can be improved somehow if needed.
We are open to any colours but we have chosen green at this stage.
Feel free to change the font and make the logo smarter looking.
Play with the colours and see what looks best.

We want a card that looks so good know one will want to throw it away!

Target Market(s)

Home buyers

Industry/Entity Type

Building

Contact Information for Business Card

Derek Tolvane
0217394062
dtolvane@quillmarkhomesteads.co.nz
quillmarkhomesteads.co.nz

Font styles to use
Serif
Sans Serif

Colors

Designer to choose colors to be used in the design.

Requirements
Must have
• Logo and company name on one side, details on the other side
Nice to have
• Color codes for the original green are HEX #4a8028, RGB(74,128,40), CMYK(42,0,69,50)
• Round corners, Raised and/or spot UV

```html
<!DOCTYPE html>
<html lang="en">
<head>
<meta charset="utf-8">
<title>Quillmark Homesteads – Business Cards</title>
<link rel="stylesheet" href="https://fonts.googleapis.com/css2?family=Open+Sans:wght@400;700;800&family=Arimo:wght@700&display=swap">
<style>
  :root {
    --brand-green: #4e8823;
    --backdrop: #c9cacc;
    --card-white: #ffffff;
    --rule-grey: #6d6e70;
    --text-light: #ffffff;
    --card-shadow: 0 3px 8px rgba(0,0,0,0.25);
  }
  * { margin: 0; padding: 0; box-sizing: border-box; }
  html, body {
    width: 1200px; height: 1015px; overflow: hidden;
    background: var(--backdrop);
    font-family: "Open Sans", sans-serif;
  }
  .stage { position: relative; width: 1200px; height: 1015px; }
  .card {
    position: absolute; width: 687px; height: 393px;
    border-radius: 22px; overflow: hidden; box-shadow: var(--card-shadow);
  }
  /* details side */
  .card--details { left: 442px; top: 79px; background: var(--card-white); }
  .details__band {
    position: absolute; left: 0; right: 0; top: 249px; bottom: 0;
    background: var(--brand-green);
  }
  .details__rule {
    position: absolute; left: 0; right: 0; top: 240px; height: 5px;
    background: var(--rule-grey);
  }
  .details__notch { position: absolute; left: 93px; top: 243px; width: 32px; height: 20px; }
  .wordmark {
    position: absolute; text-align: center;
    font-family: "Open Sans", sans-serif; font-weight: 800;
    letter-spacing: -0.5px; line-height: 1.05;
  }
  .wordmark--front {
    left: 20px; width: 290px; top: 118px; font-size: 31px; color: var(--brand-green);
  }
  .wordmark__rule { position: absolute; height: 1.5px; }
  .wordmark__rule--front { left: 108px; width: 121px; top: 191px; background: var(--brand-green); }
  .person {
    position: absolute; left: 36px; top: 296px;
    font-family: "Arimo", sans-serif; font-weight: 700;
    color: var(--text-light); font-size: 26px; line-height: 33px;
  }
  .contact { position: absolute; left: 278px; top: 279px; list-style: none; }
  .contact li {
    display: flex; align-items: center; height: 31px;
    color: var(--text-light); font-size: 17.5px; letter-spacing: -0.3px;
  }
  .contact svg { width: 16px; height: 16px; margin-right: 8px; flex: none; }
  /* logo side */
  .card--brand { left: 116px; top: 530px; background: var(--brand-green); }
  .wordmark--back {
    left: 0; width: 687px; top: 155px; font-size: 46px; color: var(--text-light);
  }
  .wordmark__rule--back { left: 249px; width: 162px; top: 275px; background: var(--text-light); }
  .brand__web {
    position: absolute; left: 0; width: 687px; top: 344px; text-align: center;
    color: var(--text-light); font-size: 16px; letter-spacing: 2.6px;
  }
</style>
</head>
<body>
<main class="stage">
  <section class="card card--details" aria-label="Business card, details side">
    <div class="wordmark wordmark--front">quillmark<br>homesteads.</div>
    <div class="wordmark__rule wordmark__rule--front"></div>
    <div class="details__band"></div>
    <div class="details__rule"></div>
    <svg class="details__notch" viewBox="0 0 32 20" aria-hidden="true">
      <polygon points="0,0 32,0 16,13" fill="var(--rule-grey)"/>
      <polyline points="2,5 16,16 30,5" fill="none" stroke="#fff" stroke-width="3"/>
    </svg>
    <div class="person">
      <div class="person__name">Derek Tolvane</div>
      <div class="person__title">Title</div>
    </div>
    <ul class="contact">
      <li>
        <svg viewBox="0 0 16 16" aria-hidden="true"><circle cx="8" cy="8" r="7" fill="none" stroke="#fff" stroke-width="1.2"/><path d="M5.5 4.5c-.8 2.8.6 6 3.6 7.2l1.2-1.6-1.6-1.2-.8.7c-1-.6-1.6-1.7-1.7-2.9l1-.4-.4-2z" fill="#fff"/></svg>
        0217394062
      </li>
      <li>
        <svg viewBox="0 0 16 16" aria-hidden="true"><path d="M1 6l7-4 7 4v8H1z" fill="#fff"/><path d="M1.5 6.5l6.5 4 6.5-4" fill="none" stroke="var(--brand-green)" stroke-width="1.2"/></svg>
        dtolvane@quillmarkhomesteads.co.nz
      </li>
      <li>
        <svg viewBox="0 0 16 16" aria-hidden="true" fill="none" stroke="#fff" stroke-width="1"><circle cx="8" cy="8" r="6.5"/><ellipse cx="8" cy="8" rx="3" ry="6.5"/><path d="M1.5 8h13M2.5 5h11M2.5 11h11"/></svg>
        www.quillmarkhomesteads.co.nz
      </li>
    </ul>
  </section>

  <section class="card card--brand" aria-label="Business card, logo side">
    <div class="wordmark wordmark--back">quillmark<br>homesteads.</div>
    <div class="wordmark__rule wordmark__rule--back"></div>
    <div class="brand__web">www.quillmarkhomesteads.co.nz</div>
  </section>
</main>
</body>
</html>
```